Summit Builders Web Site / Business Cards

Construction Company that specializes in Water and Fire Damage, Residential ReModels, Landscaping and Building ADU (Accessory Dwelling Unit)

Growing and changing families often need additional space, and a remodeling project can often provide that. Adding a new area, or repurposing an existing one can satisfy this requirement.

Other times, homeowners want to update the look in their kitchen or bathroom with more than just a change of cabinetry or vanity doors and drawers. Whatever your needs are, Summit Builders has skilled workers who are bonded and insured, and ready to make your dreams and visions a reality.

Target Market(s)

Home Owners

Industry/Entity Type

Construction Company

Contact Information for Business Card

Center Logo with our information on the corners

Back side to be Logo Only
Contact Info
CSLB License # 2418596
info@summitbuildersca.example
www.summitbuildersca.example

Coding

Coded - Design and coding required

Number of Pages Required

5+ page

Font styles to use
Serif
Sans Serif

Requirements
Must have
• Using our Logo Colors
Home
About Us
Services
Projects / Portfolio
Contact Us
Nice to have
• Colors matching our Logo
Should not have
• Black because it doesnt match our logo

```html
<!DOCTYPE html>
<html lang="en">
<head>
<meta charset="utf-8">
<title>Summit Builders</title>
<link href="https://fonts.googleapis.com/css2?family=Poppins:ital,wght@0,300;0,400;0,500;0,600;0,700;1,300&display=swap" rel="stylesheet">
<style>
:root{
  --orange:#f96a0e;
  --slate:#45535e;
  --slate-deep:#2f3b45;
  --ink:#2c3740;
  --text:#5a6670;
  --footer:#3a4651;
  --paper:#ffffff;
  --mist:#eceef0;
}
*{box-sizing:border-box;margin:0;padding:0}
html,body{width:1200px;height:4532px;overflow:hidden;background:var(--paper)}
body{font-family:"Poppins",sans-serif;color:var(--text)}
.page{position:relative;width:1200px;height:4532px;overflow:hidden}
.abs{position:absolute}
a{color:inherit;text-decoration:none}

/* header */
.brand{left:172px;top:34px;font-size:28px;font-weight:600;color:var(--ink);letter-spacing:1px;line-height:1.05}
.contact-item{display:flex;gap:12px;align-items:flex-start;font-size:14px;color:var(--text);line-height:1.5}
.contact-item b{display:block;font-weight:500;font-size:17px;color:var(--orange)}
.nav{left:491px;top:97px;display:flex;font-size:13px;font-weight:500;color:var(--ink)}
.nav a{margin-right:29px}
.nav a.current{color:var(--orange);text-decoration:underline;text-underline-offset:4px}

/* hero */
.hero{left:0;top:130px;width:1200px;height:565px;background:linear-gradient(160deg,#5b6470 0%,#8a7a63 35%,#c7c1b3 55%,#6f6a52 80%,#3f4a3e 100%)}
.hero-title{left:0;top:232px;width:1200px;text-align:center;color:#fff;font-weight:600}
.hero-title .big{font-size:92px;letter-spacing:12px;line-height:1}
.hero-title .sub{font-size:28px;letter-spacing:16px;margin-top:6px;font-weight:400}
.btn-ghost{left:551px;top:396px;width:98px;height:42px;border:2px solid #fff;color:#fff;font-size:14px;display:flex;align-items:center;justify-content:center}

/* welcome */
.welcome-photo{left:172px;top:769px;width:312px;height:332px;background:linear-gradient(135deg,#c9b89a,#8c7a5e 60%,#5d5648)}
.welcome-frame{left:204px;top:800px;width:308px;height:330px;border:5px solid var(--orange)}
.welcome-text{left:549px;top:798px;width:480px}
.kicker{font-size:19px;color:var(--ink);font-weight:400}
.heading{font-size:30px;font-weight:600;color:var(--orange);line-height:1.2}
.welcome-text p{font-size:11.5px;line-height:20px;color:var(--text);margin-top:16px}
.welcome-text .heading{margin-top:2px;margin-bottom:6px}
.btn-solid{left:551px;top:1056px;width:102px;height:48px;background:var(--orange);color:#fff;font-size:14px;font-weight:500;display:flex;align-items:center;justify-content:center;box-shadow:0 3px 6px rgba(0,0,0,.2)}

/* services */
.services{left:0;top:1230px;width:1200px;height:1172px;background:var(--slate)}
.services svg{position:absolute;left:0;top:0}
.sec-head{width:1200px;text-align:center;left:0}
.sec-head .kicker{font-size:17px}
.sec-head .heading{font-size:28px}
.card-text{position:absolute;width:240px;text-align:center}
.card-text h3{font-size:17px;font-weight:500;color:var(--ink);line-height:22px;white-space:nowrap}
.card-text h3.accent{color:var(--orange)}
.card-text p{font-size:11px;line-height:18px;color:var(--text);width:150px;margin:6px auto 0}
.centre-name{left:0;top:536px;width:1200px;text-align:center;color:var(--ink);font-weight:600}
.centre-name .big{font-size:48px;letter-spacing:3px;line-height:1}
.centre-name .sub{font-size:14px;letter-spacing:6px;margin-top:4px}

/* portfolio */
.head-left .kicker{font-size:17px}

/* values */
.value-card{width:405px;height:198px;background:#fff;box-shadow:0 0 12px rgba(0,0,0,.14);padding:22px 40px}
.value-card h3{font-size:19px;font-weight:500;color:var(--ink);margin-top:10px}
.value-card p{font-size:11.5px;line-height:19px;color:var(--text);margin-top:8px}

/* testimonials */
.testi-left{left:0;top:3698px;width:598px;height:460px;background:var(--orange)}
.testi-right{left:598px;top:3698px;width:602px;height:460px;background:var(--mist)}
.quote-mark{font-size:64px;font-weight:700;line-height:1;font-style:italic}
.quote{font-size:11.5px;line-height:19px;font-style:italic;font-weight:300}
.cite{font-size:15px;margin-top:14px}
.cite small{display:block;font-size:11px}

/* footer */
.footer-name{left:172px;top:4300px;color:#fff;font-weight:600}
.footer-name .big{font-size:42px;letter-spacing:2px;line-height:1}
.footer-name .sub{font-size:14px;letter-spacing:6px;margin-top:4px;font-weight:400}
.foot-title{font-size:22px;font-weight:500;color:#fff}
.foot-links a{display:block;color:#fff;font-size:15px;line-height:26.5px}
.foot-row{display:flex;align-items:center;gap:10px;color:#fff;font-size:15px;font-weight:500}
.rule{left:172px;top:4459px;width:856px;height:1px;background:#8a96a0}
.copyright{left:0;top:4488px;width:1200px;text-align:center;color:#fff;font-size:13px}
</style>
</head>
<body>
<div class="page">

  <!-- Header -->
  <div class="abs brand">SUMMIT<br>BUILDERS</div>
  <div class="abs contact-item" style="left:540px;top:22px">
    <svg width="36" height="36" viewBox="0 0 24 24" fill="none" stroke="var(--orange)" stroke-width="1.6"><path d="M5 3h4l2 5-2.5 1.5a11 11 0 0 0 6 6L16 13l5 2v4a2 2 0 0 1-2 2A16 16 0 0 1 3 5a2 2 0 0 1 2-2z"/></svg>
    <div>CSLB License<b># 2418596</b></div>
  </div>
  <div class="abs contact-item" style="left:709px;top:22px">
    <svg width="26" height="38" viewBox="0 0 16 24" fill="none" stroke="var(--orange)" stroke-width="1.6"><rect x="1" y="1" width="14" height="22" rx="2"/><path d="M4 8l4 3 4-3M4 8h8v6H4z"/></svg>
    <div>Email Us At:<b>info@summitbuildersca.example</b></div>
  </div>
  <nav class="abs nav">
    <a class="current" href="#">HOME</a><a href="#">ABOUT US</a><a href="#">SERVICES</a><a href="#">PROJECTS/ PORTFOLIO</a><a href="#">CONTACT US</a>
  </nav>

  <!-- Hero -->
  <div class="abs hero" role="img" aria-label="Photo of construction workers in hard hats looking up at building site"></div>
  <svg class="abs" style="left:0;top:600px" width="1200" height="100" viewBox="0 0 1200 100">
    <polygon points="0,70 600,18 1200,70 1200,100 0,100" fill="#fff"/>
  </svg>
  <div class="abs hero-title"><div class="big">SUMMIT</div><div class="sub">BUILDERS</div></div>
  <a class="abs btn-ghost" href="#">Read More</a>

  <!-- Welcome -->
  <div class="abs welcome-frame"></div>
  <div class="abs welcome-photo" role="img" aria-label="Photo of two builders cutting timber with a circular saw"></div>
  <div class="abs welcome-text">
    <div class="kicker">Welcome to</div>
    <div class="heading">SUMMIT BUILDERS</div>
    <p>Growing and changing families often need additional space, and a remodeling project can often provide that. Adding a new area, or repurposing an existing one, can satisfy this requirement for the whole household.</p>
    <p>Whatever your needs are, from kitchen and bathroom updates to a new ADU, Summit Builders has skilled workers who are bonded and insured, and ready to make your visions a reality.</p>
  </div>
  <a class="abs btn-solid" href="#">Read More</a>

  <!-- Services -->
  <section class="abs services">
    <svg width="1200" height="1172" viewBox="0 0 1200 1172">
      <polygon points="0,380 600,500 1200,380 1200,846 600,987 0,846" fill="#fff"/>
      <!-- card frames: cx,cy = (315,413) (600,335) (883,413) (315,784) (600,868) (883,784) -->
      <g stroke-width="12" fill="none" stroke-linecap="square">
        <g transform="translate(315 413)"><path d="M-146,-20 L0,-166" stroke="var(--slate-deep)"/><path d="M0,-166 L146,-20" stroke="var(--orange)"/><path d="M146,20 L0,166" stroke="var(--slate-deep)"/><path d="M0,166 L-146,20" stroke="var(--orange)"/></g>
        <g transform="translate(600 335)"><path d="M-146,-20 L0,-166" stroke="var(--slate-deep)"/><path d="M0,-166 L146,-20" stroke="var(--orange)"/><path d="M146,20 L0,166" stroke="var(--slate-deep)"/><path d="M0,166 L-146,20" stroke="var(--orange)"/></g>
        <g transform="translate(883 413)"><path d="M-146,-20 L0,-166" stroke="var(--slate-deep)"/><path d="M0,-166 L146,-20" stroke="var(--orange)"/><path d="M146,20 L0,166" stroke="var(--slate-deep)"/><path d="M0,166 L-146,20" stroke="var(--orange)"/></g>
        <g transform="translate(315 784)"><path d="M-146,-20 L0,-166" stroke="var(--slate-deep)"/><path d="M0,-166 L146,-20" stroke="var(--orange)"/><path d="M146,20 L0,166" stroke="var(--slate-deep)"/><path d="M0,166 L-146,20" stroke="var(--orange)"/></g>
        <g transform="translate(600 868)"><path d="M-146,-20 L0,-166" stroke="var(--slate-deep)"/><path d="M0,-166 L146,-20" stroke="var(--orange)"/><path d="M146,20 L0,166" stroke="var(--slate-deep)"/><path d="M0,166 L-146,20" stroke="var(--orange)"/></g>
        <g transform="translate(883 784)"><path d="M-146,-20 L0,-166" stroke="var(--slate-deep)"/><path d="M0,-166 L146,-20" stroke="var(--orange)"/><path d="M146,20 L0,166" stroke="var(--slate-deep)"/><path d="M0,166 L-146,20" stroke="var(--orange)"/></g>
      </g>
      <g fill="#fff" filter="drop-shadow(0 2px 4px rgba(0,0,0,.15))">
        <polygon transform="translate(315 413)" points="0,-152 132,-20 132,20 0,152 -132,20 -132,-20"/>
        <polygon transform="translate(600 335)" points="0,-152 132,-20 132,20 0,152 -132,20 -132,-20"/>
        <polygon transform="translate(883 413)" points="0,-152 132,-20 132,20 0,152 -132,20 -132,-20"/>
        <polygon transform="translate(315 784)" points="0,-152 132,-20 132,20 0,152 -132,20 -132,-20"/>
        <polygon transform="translate(600 868)" points="0,-152 132,-20 132,20 0,152 -132,20 -132,-20"/>
        <polygon transform="translate(883 784)" points="0,-152 132,-20 132,20 0,152 -132,20 -132,-20"/>
      </g>
      <!-- chevron badges -->
      <g>
        <g transform="translate(315 565)"><rect x="-16" y="-16" width="32" height="32" transform="rotate(45)" fill="var(--slate-deep)" stroke="#fff" stroke-width="2"/><path d="M-5,-6l5,5 5-5M-5,0l5,5 5-5" fill="none" stroke="#fff" stroke-width="2"/></g>
        <g transform="translate(600 487)"><rect x="-16" y="-16" width="32" height="32" transform="rotate(45)" fill="var(--slate-deep)" stroke="#fff" stroke-width="2"/><path d="M-5,-6l5,5 5-5M-5,0l5,5 5-5" fill="none" stroke="#fff" stroke-width="2"/></g>
        <g transform="translate(883 565)"><rect x="-16" y="-16" width="32" height="32" transform="rotate(45)" fill="var(--slate-deep)" stroke="#fff" stroke-width="2"/><path d="M-5,-6l5,5 5-5M-5,0l5,5 5-5" fill="none" stroke="#fff" stroke-width="2"/></g>
        <g transform="translate(315 936)"><rect x="-16" y="-16" width="32" height="32" transform="rotate(45)" fill="var(--slate-deep)" stroke="#fff" stroke-width="2"/><path d="M-5,-6l5,5 5-5M-5,0l5,5 5-5" fill="none" stroke="#fff" stroke-width="2"/></g>
        <g transform="translate(600 1020)"><rect x="-16" y="-16" width="32" height="32" transform="rotate(45)" fill="var(--slate-deep)" stroke="#fff" stroke-width="2"/><path d="M-5,-6l5,5 5-5M-5,0l5,5 5-5" fill="none" stroke="#fff" stroke-width="2"/></g>
        <g transform="translate(883 936)"><rect x="-16" y="-16" width="32" height="32" transform="rotate(45)" fill="var(--slate-deep)" stroke="#fff" stroke-width="2"/><path d="M-5,-6l5,5 5-5M-5,0l5,5 5-5" fill="none" stroke="#fff" stroke-width="2"/></g>
      </g>
      <!-- service icons -->
      <g fill="none" stroke-width="2.4" stroke-linejoin="round">
        <path transform="translate(315 360)" d="M0,-22 C-8,-10 -14,-2 -14,6 A14 14 0 0 0 14,6 C14,-2 8,-10 0,-22z M-6,6 a6 6 0 0 0 6,6" stroke="var(--slate-deep)"/>
        <path transform="translate(600 282)" d="M0,-22 C4,-12 12,-8 12,4 A12 12 0 0 1 -12,4 C-12,-4 -6,-8 -4,-14 C-2,-8 2,-6 0,-22z" stroke="var(--orange)"/>
        <path transform="translate(883 360)" d="M-18,20 V-2 L0,-18 18,-2 V20z M-6,20 V6 H6 V20 M10,-22 l4,4 -10,10 -4,-4z" stroke="var(--slate-deep)"/>
        <path transform="translate(315 731)" d="M0,20 V-2 M0,4 C-16,0 -16,-14 -10,-20 C-2,-16 0,-8 0,4 M0,0 C12,-2 16,-12 12,-20 C4,-18 0,-10 0,0 M-16,20 H16" stroke="var(--orange)"/>
        <path transform="translate(600 815)" d="M-20,20 V-4 L-4,-16 12,-4 V20z M-20,20 H20 M-10,20 V8 H0 V20 M4,0 H8 V6 H4z M12,-4 L20,-4 V20" stroke="var(--slate-deep)"/>
        <path transform="translate(883 731)" d="M-16,-4 H16 V20 H-16z M-16,6 H16 M-4,-4 V-18 H10 V-4 M-8,12 H-4 M4,12 H8" stroke="var(--orange)"/>
      </g>
    </svg>
    <div class="abs sec-head" style="top:52px"><div class="kicker" style="color:#fff">Summit</div><div class="heading" style="color:#fff">WHAT WE DO</div></div>
    <div class="card-text" style="left:195px;top:393px"><h3>WATER DAMAGE</h3><p>Fast drying, repair and full restoration of rooms hit by leaks or floods.</p></div>
    <div class="card-text" style="left:480px;top:315px"><h3 class="accent">FIRE DAMAGE</h3><p>Safe clean up, smoke removal and rebuilding of fire damaged homes.</p></div>
    <div class="card-text" style="left:763px;top:393px"><h3>RESIDENTIAL REMODELS</h3><p>Kitchen, bath and whole home remodels that add space and style.</p></div>
    <div class="card-text" style="left:195px;top:764px"><h3 class="accent">LANDSCAPING</h3><p>Yards, patios, planting and hardscape built to suit your family life.</p></div>
    <div class="card-text" style="left:480px;top:848px"><h3>ADU BUILDING</h3><p>Accessory dwelling units designed, permitted and built from start.</p></div>
    <div class="card-text" style="left:763px;top:764px"><h3 class="accent">KITCHEN &amp; BATH</h3><p>Updates that go beyond new cabinetry, vanity doors and drawers.</p></div>
    <div class="abs centre-name"><div class="big">SUMMIT</div><div class="sub">BUILDERS</div></div>
  </section>

  <!-- Portfolio -->
  <div class="abs head-left" style="left:241px;top:2458px"><div class="kicker">Our</div><div class="heading">PORTFOLIO</div></div>
  <svg class="abs" style="left:975px;top:2476px" width="54" height="30" viewBox="0 0 54 30">
    <polygon points="22,0 22,30 0,15" fill="var(--orange)"/><polygon points="32,0 32,30 54,15" fill="var(--slate)"/>
  </svg>
  <div class="abs" style="left:172px;top:2557px;width:294px;height:411px;background:linear-gradient(170deg,#6f9fd6,#d9d1c0 50%,#b5a98f)" role="img" aria-label="Photo of a modern school building exterior"></div>
  <div class="abs" style="left:480px;top:2557px;width:294px;height:411px;background:linear-gradient(180deg,#8fa4c4,#6f7590 45%,#6d6c70 75%,#4e4a48)" role="img" aria-label="Photo of a two-storey house with garage at dusk"></div>
  <div class="abs" style="left:788px;top:2557px;width:240px;height:197px;background:linear-gradient(180deg,#5d8fd1,#b9a597 55%,#5f8a4b)" role="img" aria-label="Photo of a brick family home with front lawn"></div>
  <div class="abs" style="left:788px;top:2771px;width:240px;height:197px;background:linear-gradient(180deg,#7aa4d4,#c9b46d 45%,#4f8a3c 75%,#3d9bb8)" role="img" aria-label="Rendering of a villa with garden and pond"></div>

  <!-- Who we are -->
  <div class="abs sec-head" style="top:3053px"><div class="kicker">Summit</div><div class="heading">WHO WE ARE</div></div>
  <div class="abs value-card" style="left:172px;top:3169px">
    <svg width="62" height="44" viewBox="0 0 62 44" fill="none" stroke="var(--orange)" stroke-width="2.2"><path d="M2 14l12-8 10 4 8-4 12 2 16 8M6 18l16 16 6 4 4-2M24 22l10 10M30 18l10 10 6-2M44 12l-14 10"/></svg>
    <h3>WE'VE REPUTION FOR EXCELLENCE</h3>
    <p style="text-align:justify">A solid educational background as a licensed Journeyman Carpenter with over 24 years of construction experience</p>
  </div>
  <div class="abs value-card" style="left:614px;top:3169px;padding-left:34px">
    <svg width="50" height="56" viewBox="0 0 50 56" fill="none" stroke="var(--orange)" stroke-width="2.2"><circle cx="25" cy="20" r="16"/><path d="M25 11l3 6 6 1-4.5 4 1 6-5.5-3-5.5 3 1-6-4.5-4 6-1z M14 32l-8 18 8-2 4 6 7-14M36 32l8 18-8-2-4 6-7-14"/></svg>
    <h3 style="margin-top:4px">WE BUILD PARTNERSHIPS</h3>
    <p>Registered builder with Homeguard Warranty Council since 2005 and Licenced builder with State Licensing Board</p>
  </div>
  <div class="abs value-card" style="left:172px;top:3408px;padding-left:36px">
    <svg width="56" height="52" viewBox="0 0 56 52" fill="none" stroke="var(--orange)" stroke-width="2.2"><path d="M28 2v44M10 10h36M16 50h24M10 10L2 28h16zM46 10l-8 18h16z M2 28a8 6 0 0 0 16 0M38 28a8 6 0 0 0 16 0"/></svg>
    <h3 style="margin-top:4px">GUIDED BY COMMITMENT</h3>
    <p style="text-align:justify">Solid reputation for building quality homes &amp; structures, competitive pricing, personalized customer service.</p>
  </div>
  <div class="abs value-card" style="left:614px;top:3408px;padding-left:28px">
    <svg width="62" height="52" viewBox="0 0 62 52" fill="none" stroke="var(--orange)" stroke-width="2.2"><path d="M18 18a13 13 0 0 1 26 0z" fill="var(--orange)"/><path d="M14 50v-8a17 12 0 0 1 34 0v8zM20 22h22"/></svg>
    <h3 style="margin-top:4px">A TEAM OF PROFESSIONALS</h3>
    <p>Small business owners who are committed to the community they live and work in.</p>
  </div>

  <!-- Testimonials -->
  <div class="abs testi-left"></div>
  <div class="abs testi-right"></div>
  <div class="abs head-left" style="left:228px;top:3752px"><div class="kicker" style="color:#fff">Our</div><div class="heading" style="color:#fff">CLIENT TESTIMONIALS</div></div>
  <svg class="abs" style="left:975px;top:3768px" width="54" height="30" viewBox="0 0 54 30">
    <polygon points="22,0 22,30 0,15" fill="#fff"/><polygon points="32,0 32,30 54,15" fill="var(--slate)"/>
  </svg>
  <div class="abs" style="left:172px;top:3846px;width:400px;color:#fff">
    <div class="quote-mark">&ldquo;</div>
    <p class="quote" style="margin-top:-4px">"...and for all the wonderful work you and your crew are doing. Our team has nothing but good things to say - we are really fortunate to have found you for this project!"</p>
    <div class="cite">Daniel Reyes<small>Chairman Oakridge Group</small></div>
  </div>
  <div class="abs" style="left:630px;top:3846px;width:400px;color:var(--text)">
    <div class="quote-mark" style="color:var(--slate)">&ldquo;</div>
    <p class="quote" style="margin-top:-4px">"SummitBuilders is one of the best general contractors we've worked with. The entire team tactfully delivered a project of exceptional quality while staying on schedule."</p>
    <div class="cite" style="color:var(--ink)">Lena Hartwell<small>Project Manager</small></div>
  </div>

  <!-- Footer -->
  <svg class="abs" style="left:0;top:4040px" width="1200" height="492" viewBox="0 0 1200 492">
    <polygon points="0,88 172,28 598,108 1200,12 1200,492 0,492" fill="var(--footer)"/>
  </svg>
  <div class="abs footer-name"><div class="big">SUMMIT</div><div class="sub">BUILDERS</div></div>
  <div class="abs" style="left:419px;top:4214px">
    <div class="foot-title">QUICK LINKS</div>
    <div class="foot-links" style="margin-top:20px"><a href="#">Home</a><a href="#">About us</a><a href="#">Services</a><a href="#">Projects/ Portfolio</a><a href="#">Contact us</a></div>
  </div>
  <div class="abs" style="left:649px;top:4214px">
    <div class="foot-title">CONTACT US</div>
    <div class="foot-row" style="margin-top:20px">
      <svg width="30" height="30" viewBox="0 0 30 30" fill="none" stroke="#fff" stroke-width="1.6"><circle cx="15" cy="15" r="13"/><path d="M10 8h3l1.5 3.5-2 1.2a8 8 0 0 0 4.5 4.5l1.2-2L22 17v3a1.5 1.5 0 0 1-1.5 1.5A12 12 0 0 1 8.5 9.5 1.5 1.5 0 0 1 10 8z"/></svg>
      OFFICE : 555-014-2210
    </div>
    <div class="foot-row" style="margin-top:24px">
      <svg width="30" height="30" viewBox="0 0 30 30" fill="none" stroke="#fff" stroke-width="1.6"><circle cx="15" cy="15" r="13"/><rect x="9" y="11" width="12" height="9"/><path d="M11 11V8h8v3M11 15h8"/></svg>
      Direct : 555-017-3384 &nbsp;&nbsp; Fax : 555-019-6652
    </div>
    <div class="foot-row" style="margin-top:26px">
      <svg width="30" height="30" viewBox="0 0 30 30" fill="none" stroke="#fff" stroke-width="1.6"><circle cx="15" cy="15" r="13"/><path d="M15 23s-6-6-6-10a6 6 0 0 1 12 0c0 4-6 10-6 10z"/><circle cx="15" cy="13" r="2"/></svg>
      420 Ridgeline Ave Fairview, CA 90000
    </div>
  </div>
  <div class="abs rule"></div>
  <div class="abs copyright">Copyrights @ 2020 Summit Builders. All Rights Reserved.</div>

</div>
</body>
</html>
```